Varnex Consulting Business card design.

See our website www.varnexconsulting.example which will give you a good idea of what we are about. The font is called 'Play'.

I'd like a standout business card in keeping with the themes and branding on the website

Target Market(s)

professionals. HR directors

Industry/Entity Type

Business

Contact Information for Business Card

Varnex Consulting PO Box 3172 Merrowdale NSW 2291 1300 485 193 Gavin Threlkeld Principal email: career@varnexconsulting.example ABN: 71203948865

Font styles to use
Other font styles liked:
• Play

Requirements
Must have
• Must have same design colours and branding as website.
• On back I'd prefer a list of the things we do which appears below the name at the header on the website

```html
<!DOCTYPE html>
<html lang="en">
<head>
<meta charset="utf-8">
<title>Varnex Consulting – Business Card</title>
<link href="https://fonts.googleapis.com/css2?family=Play:wght@400;700&display=swap" rel="stylesheet">
<style>
  :root {
    --stage: #e9e7e3;
    --navy: #0c2235;
    --navy-deep: #08192a;
    --ice-top: #c5c9e6;
    --ice-bottom: #e7e9f5;
    --logo: #e4e9ee;
    --accent: #2f86c6;
    --tagline: #2c6a98;
    --name: #1f6fae;
    --ink: #2f3238;
    --snow: #f4f6fb;
  }
  html, body {
    margin: 0;
    width: 1200px;
    height: 902px;
    overflow: hidden;
    background: var(--stage);
    font-family: "Play", sans-serif;
  }
  .sheet {
    position: relative;
    width: 1200px;
    height: 902px;
  }
  .card {
    position: absolute;
    left: 270px;
    width: 660px;
    height: 403px;
    box-shadow: 0 6px 18px rgba(0,0,0,0.18);
  }
  .card--back { top: 32px; }
  .card--front { top: 467px; }
  .card svg { display: block; width: 660px; height: 403px; }
  .logo-name { font-family: "Play", sans-serif; font-size: 40px; font-weight: 400; letter-spacing: 3px; fill: var(--logo); }
  .tagline { font-family: "Play", sans-serif; font-size: 12px; letter-spacing: 1px; fill: var(--tagline); }
  .person-name { font-family: "Play", sans-serif; font-size: 25px; font-weight: 700; fill: var(--name); }
  .person-detail { font-family: "Play", sans-serif; font-size: 19px; fill: var(--ink); }
  .contact { font-family: "Play", sans-serif; font-size: 15px; fill: var(--ink); }
  .contact-icon { fill: var(--accent); }
  .contact-glyph { fill: none; stroke: #ffffff; stroke-width: 1.2; }
</style>
</head>
<body>
<main class="sheet">

  <section class="card card--back" aria-label="Card back">
    <svg viewBox="0 0 660 403" xmlns="http://www.w3.org/2000/svg">
      <rect class="back-field" width="660" height="403" fill="var(--navy)"/>
      <text class="logo-name" x="330" y="200" text-anchor="middle">VARNEX CONSULTING</text>
      <text class="tagline" x="330" y="232" text-anchor="middle">Search &amp; Select | Career | Coaching | Leadership | Outplacement</text>
    </svg>
  </section>

  <section class="card card--front" aria-label="Card front">
    <svg viewBox="0 0 660 403" xmlns="http://www.w3.org/2000/svg">
      <defs>
        <linearGradient id="ice" x1="0" y1="0" x2="0" y2="1">
          <stop offset="0" stop-color="var(--ice-top)"/>
          <stop offset="1" stop-color="var(--ice-bottom)"/>
        </linearGradient>
        <radialGradient id="snowscape" cx="0.5" cy="0.45" r="0.55">
          <stop offset="0" stop-color="var(--snow)" stop-opacity="0.95"/>
          <stop offset="0.6" stop-color="#d7dbef" stop-opacity="0.6"/>
          <stop offset="1" stop-color="#d7dbef" stop-opacity="0"/>
        </radialGradient>
      </defs>

      <rect class="lower-field" width="660" height="403" fill="url(#ice)"/>

      <rect class="snow-photo" x="330" y="150" width="290" height="253" fill="url(#snowscape)"
            role="img" aria-label="Photo of a snowboarder jumping above snowy mountain peaks"/>

      <path class="wave-line" d="M0 262 C40 248 90 226 160 212 C260 192 360 222 480 188 C570 162 610 128 660 110"
            fill="none" stroke="#ffffff" stroke-opacity="0.75" stroke-width="2"/>
      <path class="header-wave" d="M0 0 H660 V96 C610 114 570 148 475 174 C360 206 255 178 155 198 C85 212 35 236 0 248 Z"
            fill="var(--navy)"/>

      <text class="logo-name" x="40" y="82">VARNEX CONSULTING</text>
      <text class="tagline" x="40" y="110">Search &amp; Select | Career | Coaching | Leadership | Outplacement</text>

      <text class="person-name" x="40" y="306">Gavin Threlkeld</text>
      <text class="person-detail" x="40" y="334">Principal</text>
      <text class="person-detail" x="40" y="362">ABN: 71203948865</text>

      <g class="contact-list">
        <text class="contact" x="606" y="238" text-anchor="end">1300 485 193</text>
        <rect class="contact-icon" x="614" y="226" width="13" height="13" rx="2"/>
        <path class="contact-glyph" d="M617 236 q3.5 -7 7 0"/>

        <text class="contact" x="606" y="264" text-anchor="end">career@varnexconsulting.example</text>
        <rect class="contact-icon" x="614" y="252" width="13" height="13" rx="2"/>
        <path class="contact-glyph" d="M616.5 255.5 h8 v6 h-8 z M616.5 255.5 l4 3.5 l4 -3.5"/>

        <text class="contact" x="606" y="290" text-anchor="end">PO Box 3172 Merrowdale NSW 2291</text>
        <rect class="contact-icon" x="614" y="278" width="13" height="13" rx="2"/>
        <path class="contact-glyph" d="M620.5 288.5 l-2.5 -4 a2.8 2.8 0 1 1 5 0 z"/>
      </g>
    </svg>
  </section>

</main>
</body>
</html>
```